Business Card Design

Company is a Commercial Building Company specialising in New Construction and existing refurbishments

Industry/Entity Type

Business

Contact Information for Business Card

Liam Porter
Construction Manager
E Liam@marshbuilding.com.au
M 0400 213 594
Mail 14 Tarrant Rise Kinross Bay WA 6090

```html
<!DOCTYPE html>
<html lang="en">
<head>
<meta charset="utf-8">
<title>Marsh Building &amp; Construction – Business Card</title>
<link rel="stylesheet" href="https://fonts.googleapis.com/css2?family=Saira:wdth,wght@125,300;125,700&family=Montserrat:wght@400;500&display=swap">
<style>
  :root {
    --backdrop: #e9e6e1;
    --navy-light: #76839f;
    --navy: #4a5570;
    --navy-dark: #323b52;
    --ink: #323a52;
    --ink-soft: #4a5068;
    --gold: #e5a823;
    --teal: #12b5c6;
    --paper: #fbfbfb;
    --paper-shade: #ececec;
    --white: #ffffff;
  }
  * { box-sizing: border-box; margin: 0; padding: 0; }
  html, body {
    width: 1200px; height: 858px; overflow: hidden;
    background: var(--backdrop);
  }
  .stage {
    width: 1200px; height: 858px;
    display: flex; align-items: center; justify-content: center; gap: 64px;
  }
  .card {
    border-radius: 4px; position: relative; overflow: hidden;
    box-shadow: 0 10px 28px rgba(40, 40, 50, 0.22);
  }

  /* Front (landscape) */
  .card-front {
    width: 540px; height: 310px;
    background: radial-gradient(ellipse at 55% 45%, var(--navy-light) 0%, var(--navy) 50%, var(--navy-dark) 100%);
    display: flex; align-items: center; justify-content: center;
  }
  .front-wordmark {
    font-family: "Saira", sans-serif; font-stretch: 125%; color: var(--white);
    line-height: 1.02; letter-spacing: 0.01em; font-weight: 400;
  }
  .front-wordmark .line-main { display: block; font-size: 44px; font-weight: 700; }
  .front-wordmark .line-sub { display: block; font-size: 41px; font-weight: 300; }

  /* Back (portrait) */
  .card-back {
    width: 310px; height: 540px;
    background: linear-gradient(160deg, var(--paper) 0%, var(--paper) 60%, var(--paper-shade) 100%);
  }
  .back-brand {
    position: absolute; left: 30px; top: 150px;
    display: flex; align-items: center; gap: 10px;
  }
  .brand-square { width: 14px; height: 14px; background: var(--teal); flex: none; }
  .brand-name {
    font-family: "Saira", sans-serif; font-stretch: 125%; color: var(--ink);
    line-height: 1.0;
  }
  .brand-name .line-main { display: block; font-size: 21px; font-weight: 700; }
  .brand-name .line-sub { display: block; font-size: 19.5px; font-weight: 300; }
  .person { position: absolute; left: 84px; top: 238px; }
  .person-name {
    font-family: "Saira", sans-serif; font-stretch: 125%; font-weight: 700;
    color: var(--gold); font-size: 17px; letter-spacing: 0.01em;
  }
  .person-role {
    font-family: "Montserrat", sans-serif; font-weight: 500; color: var(--ink-soft); font-size: 11px; margin-top: 1px;
  }
  .contact, .address {
    position: absolute; left: 84px;
    font-family: "Montserrat", sans-serif; color: var(--ink); font-size: 12px; line-height: 1.55;
  }
  .contact { top: 322px; }
  .address { top: 392px; }
  .footer-band {
    position: absolute; left: 0; right: 0; bottom: 0; height: 40px;
    background: var(--teal); border-top: 3px solid var(--gold);
  }
</style>
</head>
<body>
  <main class="stage">
    <section class="card card-front" aria-label="Card front">
      <h1 class="front-wordmark">
        <span class="line-main">MARSH BUILDING</span>
        <span class="line-sub">&amp; CONSTRUCTION</span>
      </h1>
    </section>

    <section class="card card-back" aria-label="Card back">
      <div class="back-brand">
        <span class="brand-square" aria-hidden="true"></span>
        <p class="brand-name">
          <span class="line-main">MARSH BUILDING</span>
          <span class="line-sub">&amp; CONSTRUCTION</span>
        </p>
      </div>
      <div class="person">
        <p class="person-name">LIAM PORTER</p>
        <p class="person-role">Construction Manager</p>
      </div>
      <div class="contact">
        <p>0400 213 594</p>
        <p>Liam@marshbuilding.com.au</p>
      </div>
      <div class="address">
        <p>14 Tarrant Rise</p>
        <p>Kinross Bay WA 6090</p>
      </div>
      <div class="footer-band" aria-hidden="true"></div>
    </section>
  </main>
</body>
</html>
```